Brackenford Fluidworks needs a website describing the repair business we are in.

Brackenford Fluidworks is a full hydraulic repair facility. We have 2 shops. We repair and service all hydraulic cylinders, pneumatic cylinders, hydraulic pumps, motors, valves and gearboxes. Our services range from large industrial plants to the individual that owns one piece of equipment. We also offer removal and install of cylinders. Along with free pick up and delivery, within a certain distance which is usually 100 miles from one of our shops.

With over 30 years experience in the hydraulic business, we can repair or replace any job. There is not a job too big or too small, we service them all.

We have customers that send whole pieces of equipment to us to do complete overhauls on all the hydraulics. Ranging from a country club green roller to a 10 ton boom truck.

Target Market(s)

Industrial plants, road builders, dirt work companies, general contractors, owners of industrial equipment (bulldozers, excavators, loaders, scrapers, motor graders, etc.

Industry/Entity Type

Hydraulic

Number of Pages Required

5+ page

Font styles to use
Sans Serif

Colors
ec1f27
ffffff
aaaaaa

Requirements
Must have
• Information about what we offer and pictures of jobs completed.
Nice to have
• Nice stock photos of jobsites and industrial plants.
Should not have
• Any sort of comical characters.

```html
<!DOCTYPE html>
<html lang="en">
<head>
<meta charset="utf-8">
<title>Brackenford Fluidworks</title>
<link rel="stylesheet" href="https://fonts.googleapis.com/css2?family=Montserrat:wght@400;500;700;800&display=swap">
<style>
  :root {
    --red: #ec1f27;
    --brand-red: #d0202e;
    --white: #ffffff;
    --grey: #aaaaaa;
    --text: #222222;
    --muted: #6b6b6b;
    --band: #f0f0f0;
    --footer: #333333;
    --footer-text: #b9b9b9;
  }
  * { margin: 0; padding: 0; box-sizing: border-box; }
  html, body { width: 826px; height: 1200px; overflow: hidden; }
  body { font-family: "Montserrat", Arial, sans-serif; color: var(--text); background: var(--white); position: relative; }

  .site-header { position: absolute; top: 0; left: 0; width: 826px; height: 109px; }
  .brand { position: absolute; left: 90px; top: 30px; display: flex; align-items: center; gap: 8px; }
  .brand-dot { width: 34px; height: 34px; border-radius: 50%; background: var(--brand-red); }
  .brand-name { font-size: 13px; font-weight: 700; color: var(--brand-red); line-height: 1.15; width: 100px; }
  .header-email { position: absolute; right: 92px; top: 28px; font-size: 13px; font-weight: 500; display: flex; align-items: center; gap: 6px; }
  .main-nav { position: absolute; right: 92px; top: 72px; display: flex; gap: 22px; font-size: 8px; font-weight: 500; letter-spacing: .3px; }
  .main-nav a { color: #333; text-decoration: none; }
  .main-nav a.active { color: var(--red); }

  .hero { position: absolute; top: 109px; left: 0; width: 826px; height: 313px;
    background: radial-gradient(ellipse at 55% 80%, #e0581c 0%, #a8361a 25%, #4b3a3c 55%, #3a4250 100%); }
  .hero-title { position: absolute; left: 90px; top: 60px; color: #111; }
  .hero-title h1 { font-size: 27px; font-weight: 800; letter-spacing: .2px; line-height: 1; }
  .hero-title p { font-size: 18px; font-weight: 500; margin-top: 4px; }
  .hero-arrow { position: absolute; top: 143px; width: 22px; height: 28px; background: var(--red); display: flex; align-items: center; justify-content: center; }
  .hero-arrow.prev { left: 0; }
  .hero-arrow.next { right: 0; }

  .intro { position: absolute; top: 474px; left: 0; width: 826px; text-align: center; }
  .intro-lead { font-size: 12px; font-weight: 500; }
  .intro-heading { font-size: 18px; font-weight: 500; color: var(--muted); margin-top: 4px; }

  .services { position: absolute; top: 530px; left: 91px; width: 644px; display: flex; justify-content: space-between; }
  .service { width: 110px; text-align: center; }
  .service-photo { width: 110px; height: 88px; }
  .service-label { color: var(--brand-red); font-size: 11px; font-weight: 500; margin-top: 5px; line-height: 1.3; }

  .about { position: absolute; top: 669px; left: 90px; width: 646px; text-align: center; font-size: 11.2px; font-weight: 500; line-height: 1.3; }
  .about p + p { margin-top: 14px; }

  .projects { position: absolute; top: 853px; left: 0; width: 826px; height: 280px; background: var(--band); }
  .projects h2 { position: absolute; top: 50px; width: 100%; text-align: center; font-size: 18px; font-weight: 500; color: var(--brand-red); }
  .project-photo { position: absolute; top: 89px; width: 205px; height: 137px; }
  .carousel-arrow { position: absolute; top: 148px; }

  .site-footer { position: absolute; top: 1133px; left: 0; width: 826px; height: 67px; background: var(--footer); color: var(--footer-text); }
  .footer-links { position: absolute; left: 91px; top: 19px; font-size: 7px; display: flex; gap: 6px; }
  .footer-links span.sep { color: #888; }
  .copyright { position: absolute; left: 91px; top: 38px; font-size: 7px; }
  .social { position: absolute; right: 91px; top: 24px; display: flex; gap: 5px; }
  .social span { width: 18px; height: 18px; border-radius: 50%; display: block; }
  .social .one { background: #3b5fb0; }
  .social .two { background: #2ea6e6; }
</style>
</head>
<body>
  <header class="site-header">
    <div class="brand">
      <span class="brand-dot"></span>
      <span class="brand-name">Brackenford Fluidworks</span>
    </div>
    <div class="header-email">
      <svg width="11" height="9" viewBox="0 0 11 9"><rect x="0" y="0" width="11" height="9" rx="1" fill="#222"/><path d="M1 1.5 L5.5 5 L10 1.5" stroke="#fff" stroke-width="1.2" fill="none"/></svg>
      info@brackenfordfluidworks
    </div>
    <nav class="main-nav">
      <a class="active" href="#">HOME</a>
      <a href="#">ABOUT US</a>
      <a href="#">SERVICES</a>
      <a href="#">PROJECTS</a>
      <a href="#">CONTACT US</a>
    </nav>
  </header>

  <section class="hero" role="img" aria-label="Industrial plant lit up at dusk under a stormy sky">
    <div class="hero-title">
      <h1>PHASELLUS</h1>
      <p>Blandit Quam</p>
    </div>
    <div class="hero-arrow prev"><svg width="10" height="14" viewBox="0 0 10 14"><path d="M8 1 L2 7 L8 13" stroke="#fff" stroke-width="2.4" fill="none"/></svg></div>
    <div class="hero-arrow next"><svg width="10" height="14" viewBox="0 0 10 14"><path d="M2 1 L8 7 L2 13" stroke="#fff" stroke-width="2.4" fill="none"/></svg></div>
  </section>

  <section class="intro">
    <p class="intro-lead">Brackenford Fluidworks is a full hydraulic repair facility. We have 2 shops.</p>
    <h2 class="intro-heading">We repair and service all...</h2>
  </section>

  <section class="services">
    <div class="service">
      <div class="service-photo" role="img" aria-label="Yellow hydraulic cylinder close-up" style="background: linear-gradient(135deg, #c9a20a, #e8c31c 45%, #3c3424);"></div>
      <p class="service-label">Hydraulic Cylinders</p>
    </div>
    <div class="service">
      <div class="service-photo" role="img" aria-label="Pneumatic cylinders resting on wooden blocks" style="background: linear-gradient(160deg, #6b6660, #c9c9c9 50%, #8a857c);"></div>
      <p class="service-label">Pneumatic<br>Cylinders</p>
    </div>
    <div class="service">
      <div class="service-photo" role="img" aria-label="Hydraulic pumps on a wooden pallet" style="background: linear-gradient(160deg, #b8ab92, #7f8184 50%, #c7b697);"></div>
      <p class="service-label">Hydraulic Pumps</p>
    </div>
    <div class="service">
      <div class="service-photo" role="img" aria-label="Hydraulic motor on a pallet" style="background: linear-gradient(160deg, #2a2a2a, #8c7a5c 55%, #3b4a80);"></div>
      <p class="service-label">Motors</p>
    </div>
    <div class="service">
      <div class="service-photo" role="img" aria-label="Red valve bodies and gearbox parts" style="background: linear-gradient(170deg, #2d2d2d, #b5523f 45%, #3a3a3a);"></div>
      <p class="service-label">Valves and<br>Gearboxes</p>
    </div>
  </section>

  <section class="about">
    <p>Our services range from large industrial plants to the individual that owns one piece of equipment. We also offer re-moval and install of cylinders. Along with free pick up and delivery, within a certain distance which is usually 100 miles from one of our shops.</p>
    <p>With over 30 years experience in the hydraulic business, we can repair or replace any job. There is not a job too big or too small, we service them all.</p>
    <p>We have customers that send whole pieces of equipment to us to do complete overhauls on all the hydraulics. Ranging from a country club green roller to a 10 ton boom truck.</p>
  </section>

  <section class="projects">
    <h2>Projects</h2>
    <svg class="carousel-arrow" style="left:33px" width="10" height="16" viewBox="0 0 10 16"><path d="M8 1 L2 8 L8 15" stroke="#333" stroke-width="1.6" fill="none"/></svg>
    <div class="project-photo" style="left:91px; background: linear-gradient(170deg, #9a9a98, #2a2a2a 45%, #a7a6a2);" role="img" aria-label="Repaired black hydraulic cylinders on a shop floor"></div>
    <div class="project-photo" style="left:310px; background: linear-gradient(175deg, #8e8a84, #5b5a58 55%, #2d2d2d);" role="img" aria-label="Cylinder assembly on a workbench"></div>
    <div class="project-photo" style="left:530px; background: linear-gradient(170deg, #b6ada0, #a1483c 50%, #8d8a85);" role="img" aria-label="Red hydraulic cylinders on pallets"></div>
    <svg class="carousel-arrow" style="left:783px" width="10" height="16" viewBox="0 0 10 16"><path d="M2 1 L8 8 L2 15" stroke="#333" stroke-width="1.6" fill="none"/></svg>
  </section>

  <footer class="site-footer">
    <div class="footer-links">
      <span>Home</span><span class="sep">|</span><span>About Us</span><span class="sep">|</span><span>Services</span><span class="sep">|</span><span>Projects</span><span class="sep">|</span><span>Contact Us</span>
    </div>
    <p class="copyright">Copyright © 2018 Brackenford Fluidworks. All rights reserved.</p>
    <div class="social"><span class="one"></span><span class="two"></span></div>
  </footer>
</body>
</html>
```